MintVela business cards

We want to create two sets of cards. One general card for mintvela [staff] and one card for the founder of the company. Below is the general/basic information for you to format/display on side of the cards:
--Company address: 418 Larkmoor Street, New York, NY 10087
--Main phone: 212-736-5182
Will also provide you with secondary 1-800 number
--company website: www.mintvela.example
--email address for general card: frontdesk@mintvela.example
--email address (for dr hollings's card: md@mintvela.example
--titles for dr hollings's card: Founder, Medical Director
--Dr. Hollings's name on the card should read: Gregor T. Hollings, MD
You can also play around with mintvela's tag line: Quiet Glow Keeps Its Promise (TM or R should be attached as a trademark has been filed)
Reason: More time to design something awesome. This company is an aesthetic medical company that offers cool and safe cosmetic treatments
For the business card design for the doctor, please change the doctor's name to look like this above his title: Gregor T. Hollings, MD instead of using Dr. Gregor....etc
Reason: WILL NOT BE ABLE TO VIEW AND FINALIZE DESIGNS UNTIL I RETURN FROM MEDICAL CONFERENCE, WHICH WILL BE ON SUNDAY/MONDAY. MY APOLOGIES
can everyone try making it very minimalistic
A Bit of a change...
Can everyone take a stab at using a grey "raw" or eco friendly stock paper. We are interested to see the designs you come up with.
Business

```html
<!DOCTYPE html>
<html lang="en">
<head>
<meta charset="utf-8">
<title>MintVela business cards</title>
<link href="https://fonts.googleapis.com/css2?family=Arimo:wght@400;700&display=swap" rel="stylesheet">
<style>
  :root {
    --backdrop-top: #f4f4f4;
    --backdrop-bottom: #d9d9d9;
    --card-white: #ffffff;
    --brand-blue: #3a9fd8;
    --brand-blue-deep: #2f8cc6;
    --ink: #2b2b2b;
    --ink-soft: #5a5a5a;
  }
  * { box-sizing: border-box; margin: 0; padding: 0; }
  html, body {
    width: 1038px; height: 1200px; overflow: hidden;
    font-family: "Arimo", Arial, sans-serif;
  }
  body {
    background: linear-gradient(180deg, var(--backdrop-top), var(--backdrop-bottom));
    position: relative;
  }
  .card {
    position: absolute; left: 99px;
    width: 840px; height: 480px;
    box-shadow: 0 6px 18px rgba(0,0,0,0.22);
  }
  .card-front { top: 80px; background: var(--card-white); }
  .card-back  { top: 630px; background: var(--brand-blue); }

  .wordmark {
    position: absolute;
    font-weight: 400; font-size: 76px; letter-spacing: -1px; line-height: 1;
  }
  .tagline {
    position: absolute;
    font-size: 10.5px; letter-spacing: 2.4px; text-transform: uppercase;
  }
  .card-front .wordmark { left: 86px; top: 206px; color: var(--brand-blue-deep); }
  .card-front .tagline  { left: 90px; top: 292px; color: var(--brand-blue-deep); }

  .card-back .wordmark { left: 0; right: 0; top: 196px; text-align: center; color: var(--card-white); }
  .card-back .tagline  { left: 0; right: 0; top: 284px; text-align: center; color: var(--card-white); }

  .contact-block { position: absolute; left: 512px; top: 100px; color: var(--ink); }
  .person-name { font-weight: 700; font-size: 21px; color: var(--brand-blue-deep); }
  .person-title { font-size: 17px; margin-top: 8px; color: var(--ink-soft); }
  .address { font-size: 17px; line-height: 27px; margin-top: 32px; }
  .contact-list { list-style: none; margin-top: 24px; }
  .contact-list li {
    display: flex; align-items: center; gap: 14px;
    font-size: 17px; height: 24.5px;
  }
  .contact-list svg { width: 13px; height: 13px; fill: var(--brand-blue); flex: none; }
</style>
</head>
<body>
  <section class="card card-front">
    <div class="wordmark">mintvela</div>
    <div class="tagline">Quiet Glow Keeps Its Promise®</div>

    <div class="contact-block">
      <p class="person-name">Gregor T. Hollings, MD</p>
      <p class="person-title">Founder, Medical Director</p>
      <p class="address">418 Larkmoor Street<br>New York, NY 10087</p>
      <ul class="contact-list">
        <li>
          <svg viewBox="0 0 16 16" aria-hidden="true"><path d="M3.5 1 6 1.5 7 5 5.3 6.4c.9 1.8 2.4 3.3 4.3 4.3L11 9l3.5 1 .5 2.5-2 2C7 14.5 1.5 9 1.5 3z"/></svg>
          212 736 5182
        </li>
        <li>
          <svg viewBox="0 0 16 16" aria-hidden="true"><path d="M3.5 1 6 1.5 7 5 5.3 6.4c.9 1.8 2.4 3.3 4.3 4.3L11 9l3.5 1 .5 2.5-2 2C7 14.5 1.5 9 1.5 3z"/></svg>
          (1 800) 212 736 5182
        </li>
        <li>
          <svg viewBox="0 0 16 16" aria-hidden="true"><path d="M1 3.5h14v9H1z M1.5 4l6.5 5 6.5-5" fill="none" stroke="#3a9fd8" stroke-width="1.6"/></svg>
          frontdesk@mintvela.example
        </li>
        <li>
          <svg viewBox="0 0 16 16" aria-hidden="true"><path d="M1 3.5h14v9H1z M1.5 4l6.5 5 6.5-5" fill="none" stroke="#3a9fd8" stroke-width="1.6"/></svg>
          md@mintvela.example
        </li>
        <li>
          <svg viewBox="0 0 16 16" aria-hidden="true"><g fill="none" stroke="#3a9fd8" stroke-width="1.4"><circle cx="8" cy="8" r="6.5"/><ellipse cx="8" cy="8" rx="2.8" ry="6.5"/><path d="M1.5 8h13"/></g></svg>
          www.mintvela.example
        </li>
      </ul>
    </div>
  </section>

  <section class="card card-back">
    <div class="wordmark">mintvela</div>
    <div class="tagline">Quiet Glow Keeps Its Promise®</div>
  </section>
</body>
</html>
```